Web Design Project for Communications Agency

The design I need (PSD file) is for an agency offering specialised PR and communications services for customers in the healthcare sector.

OBJECTIVES OF THE WEBSITE:
1. To promote the agency's communication services
2. To position Solène Brivard as an industry leader, an expert in healthcare PR and communications by highlighting blogposts and social media.

WHAT I NEED:
1st, I need the design for the Home Page ONLY.
Once approved, I will need the other pages designed as well. (Here is prototype that we've already developed for the Website that will guide you in the design:
http://qorvelle.net/solenebrivard/)

VISUAL INSPIRATION
We want to give this Website a "Flat Design" look. Here are some websites for inspiration :
- http://tavrolinkworks.com/#!/process
- http://www.brindlemoss.co/
- http://quellaroft.com/

Also, reuse images found on the company's current Website :
http://www.solenebrivard.com/fr/index.html

HOMEPAGE MAIN ELEMENTS:
1. Main menu : 6 sections
Accueil | Agence | Services | Approche | Publications | Contact

2. Main Call To Action (big dark rectangle in prototype):
Can be slider or just an information bloc.

3. Publications récentes :
The 4 latest blog posts must be features on the homepage (will be linked with the "Publications" section)

4. Dynamic Footer :
Contains a Chirpline feed and a Subscribe to our Newsletter feature (revecez nos publications)

OTHER PAGES (to design once Homepage is approved)
- Agence (about us)
- Services (our team)
- Approche (our approach)
- Publications (blog articles)
- Contact (Contact us)

Industry/Entity Type

Communications

Requirements
Must have
• Please refer to prototype :
http://qorvelle.net/solenebrivard/
Must have ALL features present in prototype.

Also, must reuse this picture in the design : http://solenebrivard.com/static/images/home-big-box.jpg

Finally, you will find attached the company logo.

```html
<!DOCTYPE html>
<html lang="fr">
<head>
<meta charset="utf-8">
<title>Solène Brivard — Gestion d'enjeux, affaires publiques</title>
<link href="https://fonts.googleapis.com/css2?family=Open+Sans:ital,wght@0,300;0,400;0,600;0,700;1,400&display=swap" rel="stylesheet">
<style>
:root{
  --red:#e0353f;
  --red-soft:rgba(224,53,63,.88);
  --ink:#3a3a3a;
  --text:#6b6b6b;
  --page:#dadada;
  --white:#ffffff;
  --hero:#383838;
  --footer:#2a2a2a;
  --bar:#121212;
  --rule:#e6e6e6;
}
*{margin:0;padding:0;box-sizing:border-box}
html,body{width:1200px;height:2553px;overflow:hidden}
body{position:relative;background:var(--page);font-family:"Open Sans",Arial,sans-serif;color:var(--text)}
.abs{position:absolute}

.topbar{left:0;top:0;width:1200px;height:39px;background:var(--bar)}
.social{display:flex;gap:6px}
.social span{width:16px;height:16px;border-radius:2px;display:block}
.s1{background:#d8483a}.s2{background:#2ca7e0}.s3{background:#3b5a9a}.s4{background:#cc2127}.s5{background:#f08a24}
.topbar .social{position:absolute;left:905px;top:11px}
.search{position:absolute;left:1033px;top:0;width:41px;height:39px;background:#3a3a3a}

.sheet{left:100px;top:63px;width:1000px;height:2122px;background:var(--white)}

.brand{left:100px;top:128px;width:1000px;text-align:center;font-size:38px;font-weight:400;color:var(--ink);line-height:1.2}

.nav{left:100px;top:252px;width:1000px;height:47px;border-top:1px solid var(--rule);display:flex;justify-content:flex-start;padding-left:208px}
.nav a{display:block;height:46px;line-height:46px;font-size:14.5px;color:#666;text-decoration:none;text-align:center;border-right:1px solid var(--rule)}
.nav a.active{background:var(--red);color:var(--white)}

.hero{left:100px;top:299px;width:1000px;height:239px;background:var(--hero)}
.hero h1{position:absolute;left:26px;top:47px;width:720px;font-size:31px;font-weight:300;color:var(--white);line-height:1.32}
.hero .btn{position:absolute;left:28px;top:152px;width:165px;height:36px;line-height:36px;text-align:center;background:var(--red);color:var(--white);font-weight:600;font-size:17px}
.hero-visual{position:absolute;left:751px;top:12px;width:225px;height:213px;background:linear-gradient(140deg,#f4f4f4 20%,#d8a0a4 45%,#c9c9c9);border-radius:6px}

.card{top:565px;width:292px;height:247px}
.card .photo{width:100%;height:100%}
.card p{position:absolute;left:0;bottom:0;width:100%;height:55px;line-height:55px;background:var(--red-soft);color:var(--white);font-size:17.5px;text-align:center}

.rule{left:126px;width:948px;height:1px;background:var(--rule)}
.section-title{left:125px;top:855px;font-size:33px;font-weight:300;color:#3a3a3a}

.post{left:126px;width:948px;height:223px}
.post .photo{position:absolute;top:0;width:213px;height:223px;border:1px solid #e2e2e2}
.post .body{position:absolute;top:2px;width:705px}
.post.left .photo{left:0}.post.left .body{left:242px}
.post.right .photo{right:0}.post.right .body{left:2px}
.post h3{font-size:21.5px;font-weight:400;color:var(--red);line-height:1.2}
.post time{display:block;font-size:15px;font-style:italic;color:#333;margin-top:1px}
.post p{font-size:13.6px;line-height:26px;margin-top:8px}
.post .more{display:inline-block;margin-top:15px;padding:0 7px;height:24px;line-height:24px;background:var(--red);color:var(--white);font-size:12px}

.footer{left:0;top:2185px;width:1200px;height:318px;background:var(--footer)}
.feed-name{position:absolute;left:128px;top:48px;font-size:38px;font-weight:600;color:var(--white);line-height:1.2}
.tweet{position:absolute;left:128px;width:520px;font-size:13.6px;line-height:22px;color:#9a9a9a}
.tweet em{font-style:normal;color:var(--red)}
.subscribe{position:absolute;left:691px;top:54px;width:383px}
.subscribe h2{font-size:28px;font-weight:400;color:var(--white)}
.subscribe label{display:block;font-size:15.5px;color:var(--white)}
.subscribe .field{height:26px;background:var(--white);border-radius:3px}
.subscribe .go{width:135px;height:33px;line-height:33px;text-align:center;background:var(--red);color:var(--white);font-size:15.5px;font-weight:600;border-radius:4px}

.legal{left:0;top:2503px;width:1200px;height:50px;background:var(--bar)}
.legal small{position:absolute;left:129px;top:16px;font-size:12.5px;color:#bbb}
.legal .social{position:absolute;left:950px;top:17px;gap:4px}
.legal .social span{width:18px;height:18px}
</style>
</head>
<body>

<header class="abs topbar">
  <div class="social"><span class="s1"></span><span class="s2"></span><span class="s3"></span><span class="s4"></span><span class="s5"></span></div>
  <div class="search"><svg width="41" height="39" viewBox="0 0 41 39"><circle cx="19" cy="18" r="5" fill="none" stroke="#bbb" stroke-width="2"/><line x1="23" y1="22" x2="27" y2="26" stroke="#bbb" stroke-width="2"/></svg></div>
</header>

<div class="abs sheet"></div>

<div class="abs brand">Solène Brivard</div>

<nav class="abs nav">
  <a class="active" style="width:89px">Accueil</a>
  <a style="width:88px">Agence</a>
  <a style="width:92px">Services</a>
  <a style="width:104px">Approche</a>
  <a style="width:119px">Publications</a>
  <a style="width:90px">Contact</a>
</nav>

<section class="abs hero">
  <h1>Cabinet-conseil en communications et affaires publiques spécialisé dans le secteur de la santé.</h1>
  <span class="btn">En savoir plus</span>
  <div class="hero-visual" role="img" aria-label="Cube blanc en trois dimensions marqué de rouge"></div>
</section>

<article class="abs card" style="left:128px">
  <div class="photo" role="img" aria-label="Illustration de molécules colorées sur fond bleu-vert" style="background:linear-gradient(135deg,#2f6f78,#b65a9a 55%,#d9a23a)"></div>
  <p>Contrary to popular belief, simply</p>
</article>
<article class="abs card" style="left:456px">
  <div class="photo" role="img" aria-label="Instruments chirurgicaux sur un plateau métallique" style="background:linear-gradient(135deg,#e8ecf2,#8e97a8 60%,#3a9aa0)"></div>
  <p>Contrary to popular belief, simply</p>
</article>
<article class="abs card" style="left:782px">
  <div class="photo" role="img" aria-label="Chirurgienne en tenue de bloc opératoire" style="background:linear-gradient(135deg,#cfe0ea,#5a8fb8 60%,#2d5d8c)"></div>
  <p>Contrary to popular belief, simply</p>
</article>

<div class="abs rule" style="top:846px"></div>
<h2 class="abs section-title">Publication récentes</h2>
<div class="abs rule" style="top:912px"></div>

<article class="abs post left" style="top:963px">
  <div class="photo" role="img" aria-label="Médecin en blouse blanche avec stéthoscope" style="background:linear-gradient(160deg,#f2f4f6,#c8d6e4)"></div>
  <div class="body">
    <h3>Titre de la publication</h3><time>23 juillet 2013</time>
    <p>Lorem ipsum dolor sit amet, consectetur adipisicing elit, sed do eiusmod tempor incididunt ut labore et dolore magna aliqua. Ut enim ad minim veniam, quis nostrud exercitation ullamco laboris nisi ut aliquip ex ea commodo consequat. Duis aute irure dolor in reprehenderit in voluptate velit esse cillum dolore eu fugiat nulla pariatur. Excepteur sint occaecat cupidatat non proident, sunt in culpa qui officia deserunt. mollit anim id est laborum.</p>
    <span class="more">READ MORE</span>
  </div>
</article>
<div class="abs rule" style="top:1234px"></div>

<article class="abs post right" style="top:1283px">
  <div class="photo" role="img" aria-label="Salle d'imagerie médicale avec écrans et table d'examen" style="background:linear-gradient(160deg,#e4e6e8,#a9b0b6)"></div>
  <div class="body">
    <h3>Titre de la publication</h3><time>23 juillet 2013</time>
    <p>Lorem ipsum dolor sit amet, consectetur adipisicing elit, sed do eiusmod tempor incididunt ut labore et dolore magna aliqua. Ut enim ad minim veniam, quis nostrud exercitation ullamco laboris nisi ut aliquip ex ea commodo consequat. Duis aute irure dolor in reprehenderit in voluptate velit esse cillum dolore eu fugiat nulla pariatur. Excepteur sint occaecat cupidatat non proident, sunt in culpa qui officia deserunt. mollit anim id est laborum.</p>
    <span class="more">READ MORE</span>
  </div>
</article>
<div class="abs rule" style="top:1552px"></div>

<article class="abs post left" style="top:1598px">
  <div class="photo" role="img" aria-label="Fioles de vaccin et seringue sur fond bleu" style="background:linear-gradient(160deg,#e6f0fb,#7fa7d6)"></div>
  <div class="body">
    <h3>Titre de la publication</h3><time>23 juillet 2013</time>
    <p>Lorem ipsum dolor sit amet, consectetur adipisicing elit, sed do eiusmod tempor incididunt ut labore et dolore magna aliqua. Ut enim ad minim veniam, quis nostrud exercitation ullamco laboris nisi ut aliquip ex ea commodo consequat. Duis aute irure dolor in reprehenderit in voluptate velit esse cillum dolore eu fugiat nulla pariatur. Excepteur sint occaecat cupidatat non proident, sunt in culpa qui officia deserunt. mollit anim id est laborum.</p>
    <span class="more">READ MORE</span>
  </div>
</article>
<div class="abs rule" style="top:1869px"></div>

<article class="abs post right" style="top:1917px">
  <div class="photo" role="img" aria-label="Gélules rouges et blanches en vrac" style="background:linear-gradient(160deg,#f1e4d2,#d4472f 55%,#7a2a1c)"></div>
  <div class="body">
    <h3>Titre de la publication</h3><time>23 juillet 2013</time>
    <p>Lorem ipsum dolor sit amet, consectetur adipisicing elit, sed do eiusmod tempor incididunt ut labore et dolore magna aliqua. Ut enim ad minim veniam, quis nostrud exercitation ullamco laboris nisi ut aliquip ex ea commodo consequat. Duis aute irure dolor in reprehenderit in voluptate velit esse cillum dolore eu fugiat nulla pariatur. Excepteur sint occaecat cupidatat non proident, sunt in culpa qui officia deserunt. mollit anim id est laborum.</p>
    <span class="more">READ MORE</span>
  </div>
</article>

<footer class="abs footer">
  <div class="feed-name">Chirpline</div>
  <p class="tweet" style="top:126px">Velit esse cillum dolore eu fugiat nulla pariatur. Excepteur sint occaecat. cupidatat non proident. <em>@SoleneBrivard #EnjeuSanté</em></p>
  <p class="tweet" style="top:186px">Velit esse cillum dolore eu fugiat nulla pariatur. Excepteur sint occaecat. cupidatat non proident. <em>@SoleneBrivard #EnjeuSanté</em></p>
  <p class="tweet" style="top:246px">Velit esse cillum dolore eu fugiat nulla pariatur. Excepteur sint occaecat. cupidatat non proident. <em>@SoleneBrivard #EnjeuSanté</em></p>

  <form class="subscribe">
    <h2>Recevez nos publications</h2>
    <label style="margin-top:18px">Votre nom</label>
    <div class="field" style="margin-top:2px"></div>
    <label style="margin-top:9px">Votre courriel</label>
    <div class="field" style="margin-top:4px"></div>
    <div class="go" style="margin-top:18px">Abonnez-vous</div>
  </form>
</footer>

<div class="abs legal">
  <small>© Copyrights 2013 All rights Reserved</small>
  <div class="social"><span class="s1"></span><span class="s2"></span><span class="s3"></span><span class="s4"></span><span class="s5"></span></div>
</div>

</body>
</html>
```